Business Card: RW Office Partners - Your organised problem solver

Business Name: RW Office Partners
Website: www.rwofficepartners.com.au
Email: marisol@rwofficepartners.com.au
Mobile: 61 482 907 236
Facebook: @rwofficepartners
Instrgram: @rwofficepartners

Brading Colours:
HEX
#986474
#ddccd3
#7a8498
#c9d8e4
#000000
#ffffff

Tag Line: Your organised problem solver

Link to DRAFT website:
https://deskhelpcollective.wixsite.com/rw-office-partners

About Page from the website:
My name is Marisol Wrenfield, and I would love to assist you to become more productive in your day to day and achieve your business and personal goals.
My mission is to give you time, time to work on the important tasks of your business or to be able to spend more time with your family. I will take on the tasks you don’t have time for, don’t know well or simply don’t like to do.
I have an extensive background in Administration, Tender Coordination, Document Control, WHS and Quality Management working primarily in the Construction, Mining and Corporate World.
I am passionate about being organised, having order and making things in your life (and mine) easier! I love to watch something unfold and grow into something amazing! I am known for being the go-to problem solver, the organiser of all things, producing high standards of work even under pressure. I’m also a confident communicator, and I understand that you’re busy running your business.

Target Market(s)

Small to Medium Business who require assistance in their business by a virtual assistant.

Industry/Entity Type

Virtual Assistant

Contact Information for Business Card

Mobile: 61 482 907 236

Font styles to use
Sans Serif

Colors
ffffff

Requirements
Must have
• Branding Colours as outlined.
Contact Details as outlined.
Logo as provided.
Proper contact details - mobile, facebook, instragm, website.
Simple, Elegant, very clean looking.
Should not have
• Note cute with pictures.
Not too girly as still want to market to construction companies.

```html
<!DOCTYPE html>
<html lang="en">
<head>
<meta charset="utf-8">
<title>RW Office Partners – Business Card</title>
<link href="https://fonts.googleapis.com/css2?family=Arimo:wght@400;700&display=swap" rel="stylesheet">
<style>
  :root {
    --brand-mauve: #986474;
    --brand-slate: #7a8498;
    --paper: #ffffff;
  }
  * { margin: 0; padding: 0; box-sizing: border-box; }
  html, body {
    width: 1200px;
    height: 749px;
    overflow: hidden;
    background: var(--paper);
  }
  .card {
    position: relative;
    width: 1200px;
    height: 749px;
    background: var(--paper);
    font-family: "Arimo", Arial, sans-serif;
    color: var(--brand-slate);
  }
  .band {
    position: absolute;
    left: 0;
    width: 1200px;
    background: var(--brand-mauve);
  }
  .band--top { top: 0; height: 200px; }
  .band--bottom { top: 549px; height: 200px; }

  .contact-list {
    position: absolute;
    left: 117px;
    top: 278px;
    list-style: none;
  }
  .contact-item {
    display: flex;
    align-items: center;
    height: 48px;
    margin-bottom: 26px;
  }
  .contact-item:nth-child(2) { margin-bottom: 27px; }
  .contact-icon {
    width: 48px;
    height: 48px;
    flex: none;
  }
  .contact-text {
    margin-left: 10px;
    font-size: 27px;
    letter-spacing: 0.2px;
  }

  .social-row {
    position: absolute;
    top: 512px;
    left: 124px;
    display: flex;
    align-items: center;
    font-size: 23px;
  }
  .social-handle {
    display: flex;
    align-items: center;
  }
  .social-handle + .social-handle { margin-left: 78px; }
  .social-dot {
    width: 16px;
    height: 16px;
    border-radius: 50%;
    background: var(--brand-mauve);
    margin-right: 8px;
  }

  .brand-name {
    position: absolute;
    left: 712px;
    top: 348px;
    font-size: 40px;
    font-weight: 700;
    color: var(--brand-slate);
    letter-spacing: 0.5px;
    white-space: nowrap;
  }
</style>
</head>
<body>
<main class="card">
  <div class="band band--top" role="img" aria-label="Mauve band with a faint repeating monogram pattern"></div>

  <ul class="contact-list">
    <li class="contact-item">
      <svg class="contact-icon" viewBox="0 0 48 48" aria-hidden="true">
        <circle cx="24" cy="24" r="24" fill="var(--brand-mauve)"/>
        <rect x="10" y="15" width="28" height="19" fill="none" stroke="#fff" stroke-width="2"/>
        <path d="M10 15 L24 26 L38 15 M10 34 L20 24 M38 34 L28 24" fill="none" stroke="#fff" stroke-width="2"/>
      </svg>
      <span class="contact-text">marisol@rwofficepartners.com.au</span>
    </li>
    <li class="contact-item">
      <svg class="contact-icon" viewBox="0 0 48 48" aria-hidden="true">
        <circle cx="24" cy="24" r="24" fill="var(--brand-mauve)"/>
        <rect x="16" y="9" width="16" height="30" rx="3" fill="none" stroke="#fff" stroke-width="2"/>
        <line x1="16" y1="14" x2="32" y2="14" stroke="#fff" stroke-width="1.5"/>
        <line x1="16" y1="33" x2="32" y2="33" stroke="#fff" stroke-width="1.5"/>
        <circle cx="24" cy="36" r="1.3" fill="#fff"/>
      </svg>
      <span class="contact-text">61 482 907 236</span>
    </li>
    <li class="contact-item">
      <svg class="contact-icon" viewBox="0 0 48 48" aria-hidden="true">
        <circle cx="24" cy="24" r="24" fill="var(--brand-mauve)"/>
        <circle cx="24" cy="24" r="13" fill="none" stroke="#fff" stroke-width="2"/>
        <ellipse cx="24" cy="24" rx="6" ry="13" fill="none" stroke="#fff" stroke-width="1.6"/>
        <line x1="11" y1="24" x2="37" y2="24" stroke="#fff" stroke-width="1.6"/>
        <line x1="13" y1="17" x2="35" y2="17" stroke="#fff" stroke-width="1.4"/>
        <line x1="13" y1="31" x2="35" y2="31" stroke="#fff" stroke-width="1.4"/>
      </svg>
      <span class="contact-text">www.rwofficepartners.com.au</span>
    </li>
  </ul>

  <div class="social-row">
    <span class="social-handle"><span class="social-dot"></span>@rwofficepartners</span>
    <span class="social-handle"><span class="social-dot"></span>@rwofficepartners</span>
  </div>

  <div class="brand-name">RW Office Partners</div>

  <div class="band band--bottom" role="img" aria-label="Mauve band with a faint repeating monogram pattern"></div>
</main>
</body>
</html>
```